German Headhunter/ HR Consultancy needs Business Cards Design

We need a business Card Design for our Company in Stuttgart. We are specialized as Headhunter/ HR Consultancy in Placement of specialist and managers in permanent employment. Please refer to our business logo.

```html
<!DOCTYPE html>
<html lang="de">
<head>
<meta charset="utf-8">
<title>Kernwerk Personalberatung – Visitenkarte</title>
<link rel="stylesheet" href="https://fonts.googleapis.com/css2?family=Montserrat:wght@300;400;600;700&display=swap">
<style>
  :root {
    --brand-blue: #3a53a8;
    --brand-blue-light: #4d66b8;
    --paper: #ffffff;
    --ink: #1e1e24;
    --stage: #2b2b2d;
    --emboss: #8fa3d8;
  }
  html, body {
    margin: 0;
    padding: 0;
    width: 1200px;
    height: 1120px;
    overflow: hidden;
    background: var(--stage);
    font-family: "Montserrat", sans-serif;
  }
  .canvas {
    position: relative;
    width: 1200px;
    height: 1120px;
  }
  .card {
    position: absolute;
    left: 180px;
    width: 840px;
    height: 480px;
    overflow: hidden;
    box-shadow: 0 18px 40px rgba(0,0,0,.45);
  }
  .card-front { top: 50px; background: var(--paper); }
  .card-back {
    top: 590px;
    background: linear-gradient(160deg, var(--brand-blue) 0%, var(--brand-blue) 60%, var(--brand-blue-light) 100%);
  }

  /* front: wordmark */
  .wordmark {
    position: absolute;
    left: 60px;
    top: 58px;
    display: flex;
    align-items: center;
    gap: 16px;
    color: var(--brand-blue);
    font-weight: 600;
  }
  .wordmark-square {
    width: 44px;
    height: 44px;
    background: var(--brand-blue);
  }
  .wordmark-text { line-height: 1; }
  .wordmark-name { font-size: 38px; letter-spacing: 1px; display: block; }
  .wordmark-sub { font-size: 15px; letter-spacing: 2.4px; display: block; margin-top: 6px; }

  /* front: band and block */
  .name-band {
    position: absolute;
    left: 0;
    top: 205px;
    width: 600px;
    height: 92px;
    background: var(--brand-blue);
  }
  .feature-block {
    position: absolute;
    left: 600px;
    top: 40px;
    width: 200px;
    height: 257px;
    background: var(--brand-blue);
  }
  .holder {
    position: absolute;
    left: 60px;
    top: 219px;
    color: var(--paper);
  }
  .holder-name { margin: 0; font-size: 34px; font-weight: 700; line-height: 1.1; }
  .holder-role { margin: 4px 0 0; font-size: 17px; font-weight: 300; }

  /* front: contacts */
  .contacts {
    position: absolute;
    left: 60px;
    top: 326px;
    margin: 0;
    padding: 0;
    list-style: none;
    color: var(--ink);
    font-size: 18px;
    font-weight: 400;
  }
  .contacts li {
    display: flex;
    align-items: center;
    gap: 14px;
    height: 31px;
  }
  .contact-icon {
    width: 16px;
    height: 16px;
    flex: none;
  }

  /* back */
  .back-wordmark {
    position: absolute;
    left: 0;
    right: 0;
    top: 170px;
    display: flex;
    justify-content: center;
    align-items: center;
    gap: 20px;
    color: var(--emboss);
    font-weight: 600;
  }
  .back-wordmark .wordmark-square { width: 56px; height: 56px; background: var(--emboss); }
  .back-wordmark .wordmark-name { font-size: 52px; }
  .back-wordmark .wordmark-sub { font-size: 20px; letter-spacing: 3.4px; }
</style>
</head>
<body>
<main class="canvas">

  <section class="card card-front" aria-label="Visitenkarte Vorderseite">
    <div class="wordmark">
      <span class="wordmark-square"></span>
      <span class="wordmark-text">
        <span class="wordmark-name">KERNWERK</span>
        <span class="wordmark-sub">PERSONALBERATUNG</span>
      </span>
    </div>

    <div class="name-band"></div>
    <div class="feature-block"></div>

    <div class="holder">
      <p class="holder-name">Jonas Werner</p>
      <p class="holder-role">Geschäftsführer</p>
    </div>

    <ul class="contacts">
      <li>
        <svg class="contact-icon" viewBox="0 0 16 16" aria-hidden="true"><circle cx="8" cy="8" r="8" fill="var(--brand-blue)"/><path d="M5 4.5c.5-.5 1-.5 1.3 0l.8 1.3c.2.4 0 .8-.3 1l-.4.3c.4.9 1.1 1.6 2 2l.3-.4c.2-.3.6-.5 1-.3l1.3.8c.5.3.5.8 0 1.3-.8.8-2 .8-3.4-.2-1.2-.8-2.1-1.800-2.7-3-.6-1.2-.7-2.2.1-2.8z" fill="#fff"/></svg>
        <span>+49 1570 4418265</span>
      </li>
      <li>
        <svg class="contact-icon" viewBox="0 0 16 16" aria-hidden="true"><circle cx="8" cy="8" r="8" fill="var(--brand-blue)"/><rect x="4" y="5.5" width="8" height="5.5" fill="#fff"/><path d="M4 5.5l4 3 4-3" stroke="var(--brand-blue)" stroke-width="1" fill="none"/></svg>
        <span>kontakt@kernwerk-personal.de</span>
      </li>
      <li>
        <svg class="contact-icon" viewBox="0 0 16 16" aria-hidden="true"><circle cx="8" cy="8" r="8" fill="var(--brand-blue)"/><circle cx="8" cy="8" r="4.2" fill="none" stroke="#fff" stroke-width="1"/><ellipse cx="8" cy="8" rx="1.8" ry="4.2" fill="none" stroke="#fff" stroke-width="1"/><path d="M3.8 8h8.4" stroke="#fff" stroke-width="1"/></svg>
        <span>www.kernwerk-personal.de</span>
      </li>
      <li>
        <svg class="contact-icon" viewBox="0 0 16 16" aria-hidden="true"><circle cx="8" cy="8" r="8" fill="var(--brand-blue)"/><path d="M8 3.5a3 3 0 0 1 3 3c0 2.2-3 5.8-3 5.8S5 8.7 5 6.5a3 3 0 0 1 3-3z" fill="#fff"/><circle cx="8" cy="6.5" r="1.1" fill="var(--brand-blue)"/></svg>
        <span>Lindenstraße 14, 38124 Neudorf, Germany</span>
      </li>
    </ul>
  </section>

  <section class="card card-back" aria-label="Visitenkarte Rückseite">
    <div class="back-wordmark">
      <span class="wordmark-square"></span>
      <span class="wordmark-text">
        <span class="wordmark-name">KERNWERK</span>
        <span class="wordmark-sub">PERSONALBERATUNG</span>
      </span>
    </div>
  </section>

</main>
</body>
</html>
```